Tovel & Associates - London New Letting and Property Management Company *

Tovel & Associates LTD is a new company based in London, and works with brand new residential property in the city centre.

We are aiming to have 1000 new properties a year.

We are looking for something modern and minimalistic :
Logo ,Monogram, Paper Head and Business Card.

Target Market(s)

Internation landlords

Industry/Entity Type

Real Estate

Logo Text

Tovel & Associates

Colors

Designer to choose colors to be used in the design.

Requirements
Nice to have
• A particular monogram with "TA"
Should not have
• Little House over the logo

```html
<!DOCTYPE html>
<html lang="en">
<head>
<meta charset="UTF-8">
<title>Tovel &amp; Associates LTD – Business Card</title>
<link href="https://fonts.googleapis.com/css2?family=Montserrat:wght@500;600;700&family=Lato:wght@400&display=swap" rel="stylesheet">
<style>
  :root {
    --navy: #1c5288;
    --navy-deep: #17508a;
    --navy-emboss: #12467a;
    --sky: #1f9bd7;
    --ink: #4a4a4a;
    --paper: #ffffff;
    --backdrop: #e6e7e9;
  }
  * { box-sizing: border-box; margin: 0; padding: 0; }
  html, body {
    width: 1200px; height: 900px; overflow: hidden;
    background: var(--backdrop);
  }
  .sheet {
    width: 1200px; height: 900px;
    display: flex; flex-direction: column; align-items: center; justify-content: center;
    gap: 60px;
  }
  .card {
    width: 630px; height: 360px;
    border-radius: 22px;
    position: relative; overflow: hidden;
    box-shadow: 0 6px 18px rgba(0,0,0,0.18);
  }
  /* Back side */
  .card-back {
    background: var(--navy-deep);
    display: flex; align-items: center; justify-content: center;
  }
  .card-back .brand-name {
    font-family: "Montserrat", sans-serif;
    font-weight: 700; font-size: 34px;
    color: var(--navy-emboss);
    letter-spacing: 0.5px;
  }
  /* Front side */
  .card-front { background: var(--paper); }
  .front-brand {
    position: absolute; left: 40px; top: 128px; width: 260px;
    text-align: center;
    font-family: "Montserrat", sans-serif;
    font-weight: 700; font-size: 25px; line-height: 1.25;
    color: var(--navy);
  }
  .divider {
    position: absolute; left: 322px; top: 72px;
    width: 2px; height: 180px; background: var(--sky);
  }
  .contact {
    position: absolute; left: 348px; top: 62px;
    font-family: "Lato", sans-serif; color: var(--ink);
  }
  .person-name {
    font-family: "Montserrat", sans-serif; font-weight: 700;
    font-size: 21px; color: var(--sky); letter-spacing: 0.3px;
  }
  .person-role { font-size: 14px; margin-bottom: 12px; }
  .contact-list { list-style: none; }
  .contact-list li {
    display: flex; align-items: center; gap: 9px;
    font-size: 14px; line-height: 19px;
  }
  .contact-list svg { width: 12px; height: 12px; flex: none; }
  .address { font-size: 14.5px; line-height: 19px; margin-top: 12px; }
  .wave { position: absolute; left: 0; bottom: 0; width: 630px; height: 120px; }
</style>
</head>
<body>
<main class="sheet">
  <section class="card card-back" aria-label="Card back">
    <span class="brand-name">Tovel &amp; Associates LTD</span>
  </section>

  <section class="card card-front" aria-label="Card front">
    <div class="front-brand">Tovel &amp; Associates LTD</div>
    <div class="divider"></div>

    <div class="contact">
      <div class="person-name">ELAN HARTLEY</div>
      <div class="person-role">Founder</div>
      <ul class="contact-list">
        <li>
          <svg viewBox="0 0 12 12" fill="none" stroke="#1f9bd7" stroke-width="1.3"><rect x="3" y="1" width="6" height="10" rx="1"/><line x1="5" y1="9.3" x2="7" y2="9.3"/></svg>
          407. 528. 3194
        </li>
        <li>
          <svg viewBox="0 0 12 12" fill="#1f9bd7"><path d="M3 1.5l1.8 2.2-1 1.2c.6 1.3 1.6 2.3 2.9 2.9l1.2-1 2.2 1.8-1 1.8C5.6 10.3 1.7 6.4 1.6 2.5z"/></svg>
          407. 861. 4500
        </li>
        <li>
          <svg viewBox="0 0 12 12" fill="none" stroke="#1f9bd7" stroke-width="1.2"><rect x="1" y="2.5" width="10" height="7"/><path d="M1 2.5l5 4 5-4"/></svg>
          hello@tovelassociates.com
        </li>
        <li>
          <svg viewBox="0 0 12 12" fill="none" stroke="#1f9bd7" stroke-width="1.1"><circle cx="6" cy="6" r="5"/><ellipse cx="6" cy="6" rx="2.2" ry="5"/><line x1="1" y1="6" x2="11" y2="6"/></svg>
          www.tovelassociates.com
        </li>
      </ul>
      <div class="address">84 Larkfield Crescent<br>Brimsdale Heights, FL 32091</div>
    </div>

    <svg class="wave" viewBox="0 0 630 120" preserveAspectRatio="none" aria-hidden="true">
      <path d="M0 16 C120 6 260 20 380 70 C470 108 560 112 630 104 L630 120 L0 120 Z" fill="#1c5288"/>
      <path d="M0 10 C120 0 260 14 380 64 C470 102 560 106 630 98" fill="none" stroke="#1f9bd7" stroke-width="5"/>
    </svg>
  </section>
</main>
</body>
</html>
```